Fern Moss Cleaning Tablets needs 4 x labels

We're about to launch a very exciting cleaning product to market and need your help to brand the 4 x bottles. www.fernmossly.com.au will change the way people buy and use household cleaning products whilst significantly reducing the impact on the earth.

The tablets are dropped into the long life recycled plastic bottle, you simply add water, wait for the tab to dissolve and begin cleaning.

Target Market(s)

Women aged between 30 - 65, care for the environment, want to use less plastic, are early adopters and like to try new things. Care about a clean home and using less chemicals. Want less packaging, less plastic, less carbon emissions.

Industry/Entity Type

House Cleaning

Font styles to use
Sans Serif

Requirements
Must have
• Each label must have an obvious colour differentiator and each label must be identical in it's dimensions and information. Should look uniform when all 4 bottles are aligned in the cupboard. Limited / no images apart from logo.
Nice to have
• Simple, clear, bold, striking. Limited / no pictures. Clean lines with lots of space.
Should not have
• Sparkwell Pane Label must have a strip of blue (hex BAE1FF).
Grime Hauler Kitchen Cleaner must have a strip of colour (FFD6F3)
The Fizzer Bathroom cleaner must have a colour strip hex # FFFFBA
The Allrounder Multip Purpose must have a strip of colour Hex #BAFFC9

```html
<!DOCTYPE html>
<html lang="en">
<head>
<meta charset="utf-8">
<title>Fern Moss – Sparkwell Window Cleaner Label</title>
<link href="https://fonts.googleapis.com/css2?family=Oswald:wght@500;600&family=Sansita:ital,wght@1,800&display=swap" rel="stylesheet">
<style>
  :root {
    --page-bg: #ffffff;
    --label-blue: #a3d5f0;
    --ink-teal: #0b4a5c;
    --brand-teal: #1a8aae;
    --soft-white: #ffffff;
    --shape-white: rgba(255, 255, 255, 0.85);
  }
  html, body {
    margin: 0;
    padding: 0;
    width: 1200px;
    height: 799px;
    overflow: hidden;
    background: var(--page-bg);
  }
  .canvas {
    position: relative;
    width: 1200px;
    height: 799px;
  }
  .label {
    position: absolute;
    left: 389px;
    top: 110px;
    width: 422px;
    height: 580px;
    background: var(--label-blue);
    overflow: hidden;
    font-family: "Oswald", sans-serif;
    color: var(--ink-teal);
  }
  .decor {
    position: absolute;
    background: var(--shape-white);
  }
  .decor--top-left {
    left: 4px; top: 8px; width: 58px; height: 128px;
    border-radius: 50% 45% 50% 40%;
  }
  .decor--right {
    left: 388px; top: 55px; width: 34px; height: 275px;
    border-radius: 50% 10% 10% 50%;
  }
  .decor--left {
    left: 0; top: 215px; width: 52px; height: 325px;
    border-radius: 10% 50% 45% 20%;
  }
  .brand {
    position: absolute;
    left: 0; right: 0; top: 58px;
    display: flex;
    align-items: center;
    justify-content: center;
    gap: 10px;
  }
  .brand__dot {
    width: 22px; height: 22px;
    border-radius: 50%;
    background: var(--brand-teal);
  }
  .brand__name {
    font-weight: 600;
    font-size: 46px;
    line-height: 1;
    color: var(--brand-teal);
    letter-spacing: 1px;
  }
  .product-title {
    position: absolute;
    left: 56px; right: 40px; top: 190px;
    margin: 0;
    text-align: center;
    font-family: "Sansita", sans-serif;
    font-style: italic;
    font-weight: 800;
    font-size: 33px;
    line-height: 56px;
    white-space: nowrap;
    color: var(--ink-teal);
  }
  .waves {
    position: absolute;
    left: 97px; top: 310px;
    width: 248px; height: 70px;
  }
  .tagline {
    position: absolute;
    left: 56px; right: 40px; top: 404px;
    margin: 0;
    text-align: center;
    font-weight: 500;
    font-size: 16px;
    letter-spacing: -0.4px;
    white-space: nowrap;
  }
  .volume {
    position: absolute;
    left: 162px; top: 440px;
    width: 122px; height: 98px;
    border-radius: 46% 50% 48% 50%;
    background: var(--soft-white);
    display: flex;
    align-items: center;
    justify-content: center;
    font-weight: 600;
    font-size: 24px;
  }
  .origin {
    position: absolute;
    left: 0; right: 0; top: 548px;
    margin: 0;
    padding-left: 22px;
    text-align: center;
    font-weight: 500;
    font-size: 17px;
    letter-spacing: -0.3px;
  }
</style>
</head>
<body>
<main class="canvas">
  <section class="label">
    <div class="decor decor--top-left" role="img" aria-label="Pale white sea turtle illustration"></div>
    <div class="decor decor--right" role="img" aria-label="Pale white sea turtle illustration"></div>
    <div class="decor decor--left" role="img" aria-label="Pale white sea turtle illustration"></div>

    <div class="brand">
      <span class="brand__name">Fern Moss</span>
      <span class="brand__dot"></span>
    </div>

    <h1 class="product-title">Sparkwell’ Window<br>Cleaner</h1>

    <svg class="waves" viewBox="0 0 248 70" aria-hidden="true">
      <g fill="none" stroke="#ffffff" stroke-width="6" stroke-linecap="round">
        <path d="M3 8 Q33 -2 63 8 T124 8 T185 8 T245 8"/>
        <path d="M3 34 Q33 24 63 34 T124 34 T185 34 T245 34"/>
        <path d="M3 60 Q33 50 63 60 T124 60 T185 60 T245 60"/>
      </g>
    </svg>

    <p class="tagline">ONE BOTTLE · ONE TAB · DISSOLVE · CLEAN · REPEAT ·</p>

    <div class="volume">500 мл</div>

    <p class="origin">CORALBY · AUSTRALIA</p>
  </section>
</main>
</body>
</html>
```